Quill Petal Loft Hair Salon needs a Webpage design

Quill Petal Loft in Englewood is looking to start their web page, url and business emails, we want to be able to upload pictures and videos on the website. we do blow outs , makeup, color, lash extension, gel manicures

Target Market(s)

everyone

Industry/Entity Type

Beauty Salon

Coding

Coded - Design and coding required

Number of Pages Required

5+ page

Font styles to use
Serif

Colors
ffcf3e
9d9d9d
000000
ffffff

Requirements
Must have
• about us, contact us, products, menu, location, gallery, press
Nice to have
• play video gallery

```html
<!DOCTYPE html>
<html lang="en">
<head>
<meta charset="utf-8">
<title>Quill Petal Loft Hair Salon</title>
<link rel="stylesheet" href="https://fonts.googleapis.com/css2?family=Open+Sans:wght@300;400;600&family=Lato:wght@400&family=Playfair+Display:wght@700&display=swap">
<style>
:root{
  --gold:#ffcf3e;
  --gold-deep:#f6b93b;
  --grey:#9d9d9d;
  --black:#000000;
  --white:#ffffff;
  --ink:#222222;
  --body:#555555;
  --light-bg:#f5f5f5;
  --footer:#2b2b2b;
}
*{margin:0;padding:0;box-sizing:border-box}
html,body{width:1200px;height:2230px;overflow:hidden}
body{font-family:"Open Sans",sans-serif;color:var(--ink);background:var(--white);position:relative}
.abs{position:absolute}

/* top bar */
.topbar{left:0;top:0;width:1200px;height:46px;background:var(--black);color:var(--white);font-size:11px;letter-spacing:.3px}
.topbar .item{top:16px;display:flex;align-items:center;gap:8px}
.icon{width:10px;height:10px;fill:var(--gold)}
.social{display:flex;gap:14px;align-items:center}
.social span{width:10px;height:10px;border-radius:50%;background:var(--gold);display:block}

/* header */
.header{left:0;top:46px;width:1200px;height:124px;background:var(--white)}
.brand{font-family:"Open Sans",sans-serif;font-weight:600;color:var(--gold-deep);font-size:21px;line-height:1.1;display:flex;align-items:center;gap:8px;white-space:nowrap}
.brand i{width:12px;height:12px;border-radius:50%;background:var(--gold);display:block}
.nav{left:0;top:0;width:1200px;height:124px;font-family:"Lato",sans-serif;font-size:12px;letter-spacing:.8px}
.nav a{position:absolute;top:56px;text-decoration:none;color:var(--ink);white-space:nowrap}
.nav a.active{color:var(--gold-deep)}
.book{left:972px;top:46px;width:94px;height:34px;border:1px solid var(--ink);font-family:"Lato",sans-serif;font-size:11px;letter-spacing:.8px;display:flex;align-items:center;justify-content:center;white-space:nowrap}

/* hero */
.hero{left:0;top:170px;width:1200px;height:419px;background:linear-gradient(90deg,#a77a5b 0%,#b98f72 40%,#c9a58c 60%,#8a5f45 100%)}
.hero-photo{right:0;top:0;width:640px;height:419px;background:radial-gradient(ellipse at 70% 45%,#d8a887 0%,#a7735a 35%,#4a2e22 75%,#3a2419 100%)}
.hero-title{left:115px;width:400px;top:100px;text-align:center;font-family:"Playfair Display",serif;font-weight:700;font-size:56px;line-height:70px;letter-spacing:4px;color:var(--gold)}
.hero-sub{left:95px;width:440px;top:187px;text-align:center;color:var(--white);font-size:15px;letter-spacing:1.3px;line-height:24px}
.hero-btn{left:263px;top:258px;width:104px;height:42px;background:var(--gold);color:var(--white);font-size:10px;letter-spacing:.8px;display:flex;align-items:center;justify-content:center}
.arrow{width:48px;height:48px;background:rgba(60,40,30,.55);display:flex;align-items:center;justify-content:center;top:163px}

/* welcome */
.section-title{width:1200px;left:0;text-align:center;font-family:"Open Sans",sans-serif;font-weight:400;font-size:30px;letter-spacing:2px;color:var(--ink)}
.intro{left:131px;width:938px;top:682px;text-align:center;font-size:11px;line-height:19px;color:var(--body)}
.feature{width:300px;text-align:center}
.feature .disc{width:82px;height:82px;border-radius:50%;margin:0 auto;display:flex;align-items:center;justify-content:center;background:var(--black)}
.feature .disc.gold{background:var(--gold)}
.feature h3{font-family:"Lato",sans-serif;font-weight:400;font-size:20px;letter-spacing:2px;margin-top:25px}
.feature p{font-size:11.5px;line-height:18px;color:var(--body);margin-top:12px}
.more{font-size:10px;color:var(--ink);margin-top:12px;display:inline-block}

/* menu */
.menu{left:0;top:1028px;width:1200px;height:484px;background:var(--light-bg)}
.card{width:223px}
.card .photo{width:223px;height:126px;border:4px solid var(--white);box-shadow:0 0 0 1px #ddd}
.card h3{font-family:"Lato",sans-serif;font-weight:400;font-size:20px;letter-spacing:1.5px;margin-top:30px;padding-left:3px}
.card p{font-size:11px;line-height:19px;color:var(--body);margin-top:8px;padding-left:2px;white-space:nowrap;letter-spacing:-.1px}
.card .btn{margin-top:12px;width:79px;height:32px;background:var(--gold);border-radius:2px;font-size:10px;display:flex;align-items:center;justify-content:center;color:var(--ink)}

/* gallery */
.gallery-title{top:1550px}
.shot{top:1624px;width:299px;height:235px}

/* footer */
.footer{left:0;top:1921px;width:1200px;height:309px;background:var(--footer);color:var(--white)}
.footer .brand{color:var(--white);font-size:24px}
.footer .blurb{left:131px;top:133px;width:250px;font-size:11.5px;line-height:19px}
.footer h4{left:451px;top:34px;font-weight:400;font-size:19px;letter-spacing:1.5px}
.loc{font-size:11px;line-height:19px;display:flex;gap:12px;width:190px}
.rule{left:131px;top:239px;width:938px;height:1px;background:#555}
.copy{left:131px;top:265px;font-size:11px}
</style>
</head>
<body>

<div class="abs topbar">
  <div class="abs item" style="left:131px">
    <svg class="icon" viewBox="0 0 10 10"><path d="M2 0l2 2-1 1.5c.8 1.5 2 2.7 3.5 3.5L8 6l2 2-1.5 2C4 9.5.5 6 0 1.5z"/></svg>
    <span>201.555.0140 &nbsp;/ 201.555.0182</span>
  </div>
  <div class="abs item" style="left:334px">
    <svg class="icon" viewBox="0 0 10 10"><path d="M5 0a3.5 3.5 0 0 1 3.5 3.5C8.5 6 5 10 5 10S1.5 6 1.5 3.5A3.5 3.5 0 0 1 5 0zm0 2a1.5 1.5 0 1 0 0 3 1.5 1.5 0 0 0 0-3z"/></svg>
    <span>14 LINDEN ROW, ENGLEWOOD, NJ</span>
  </div>
  <div class="abs social" style="left:970px;top:18px"><span></span><span></span><span></span><span></span></div>
</div>

<header class="abs header">
  <div class="abs brand" style="left:131px;top:50px"><i></i>Quill Petal Loft</div>
  <nav class="abs nav">
    <a class="active" style="left:346px">HOME</a>
    <a style="left:422px">ABOUT</a>
    <a style="left:504px">MENUS</a>
    <a style="left:587px">PRODUCTS</a>
    <a style="left:693px">LOCATIONS</a>
    <a style="left:803px">PRESS</a>
    <a style="left:874px">CONTACT</a>
  </nav>
  <div class="abs book">BOOK NOW</div>
</header>

<section class="abs hero">
  <div class="abs hero-photo" role="img" aria-label="Portrait of a woman with long glossy straight brown hair"></div>
  <div class="abs arrow" style="left:55px"><svg width="12" height="20" viewBox="0 0 12 20"><path d="M10 2L2 10l8 8" stroke="#fff" stroke-width="1.5" fill="none"/></svg></div>
  <div class="abs arrow" style="left:1097px"><svg width="12" height="20" viewBox="0 0 12 20"><path d="M2 2l8 8-8 8" stroke="#fff" stroke-width="1.5" fill="none"/></svg></div>
  <div class="abs hero-title">HAIR SPA</div>
  <div class="abs hero-sub">QUILL PETAL LOFT ARE SPECIALIZED SALONS<br>DESIGNED FOR BLOWOUTS</div>
  <div class="abs hero-btn">VIEW DETAILS</div>
</section>

<h2 class="abs section-title" style="top:632px">WELCOME TO QUILL PETAL LOFT</h2>
<p class="abs intro">Quill Petal Loft are specialized salons designed for blowouts, cuts, keratin treatments, and makeup. The shops feature state of the art facilities, custom servicing anyone who wants to enjoy great looking hair! Quill Petal Loft offers affordable luxury at its finest.</p>

<div class="abs feature" style="left:98px;top:750px">
  <div class="disc gold"><svg width="24" height="24" viewBox="0 0 24 24"><path d="M4 18C4 9 10 5 20 5c0 10-5 15-13 14z" fill="#fff"/><path d="M5 19l9-9" stroke="var(--gold)" stroke-width="1.5"/></svg></div>
  <h3>AFFORDABLE</h3>
  <p>Nemo enim ipsam voluptatem quia voluptas<br>sit aspernatur aut odit aut</p>
  <span class="more">Read More ▸</span>
</div>
<div class="abs feature" style="left:449px;top:750px">
  <div class="disc"><svg width="24" height="24" viewBox="0 0 24 24"><path d="M6 18c-2-4 0-10 6-12l6-1c1 6-2 12-8 13z" fill="none" stroke="#fff" stroke-width="1.8"/></svg></div>
  <h3>LUXURY</h3>
  <p>Nemo enim ipsam voluptatem quia voluptas<br>sit aspernatur aut odit aut</p>
  <span class="more">Read More ▸</span>
</div>
<div class="abs feature" style="left:796px;top:750px">
  <div class="disc"><svg width="26" height="26" viewBox="0 0 26 26" fill="none" stroke="#fff" stroke-width="1.6"><circle cx="6" cy="8" r="3"/><circle cx="6" cy="18" r="3"/><path d="M8.5 9.5L22 18M8.5 16.5L22 8"/></svg></div>
  <h3>FINEST</h3>
  <p>Nemo enim ipsam voluptatem quia voluptas<br>sit aspernatur aut odit aut</p>
  <span class="more">Read More ▸</span>
</div>

<section class="abs menu">
  <h2 class="abs section-title" style="top:67px">OUR MENU</h2>
  <div class="abs card" style="left:131px;top:147px">
    <div class="photo" role="img" aria-label="Stylist giving a round-brush blowout" style="background:linear-gradient(120deg,#d9e3ea,#a07560 60%,#6b4433)"></div>
    <h3>BLOWOUTS</h3><p>Nemo enim ipsam voluptatem quia volup-<br>tas sit aspernatur aut odit aut</p><div class="btn">Read More ▸</div>
  </div>
  <div class="abs card" style="left:370px;top:147px">
    <div class="photo" role="img" aria-label="Stylist cutting blonde hair" style="background:linear-gradient(120deg,#e8d3a8,#d8b98a 50%,#eeeeee)"></div>
    <h3>CUTS</h3><p>Nemo enim ipsam voluptatem quia volup-<br>tas sit aspernatur aut odit aut</p><div class="btn">Read More ▸</div>
  </div>
  <div class="abs card" style="left:608px;top:147px">
    <div class="photo" role="img" aria-label="Hair being dried for a keratin treatment" style="background:linear-gradient(120deg,#c9d4d8,#9a6a4f 50%,#d4d9dc)"></div>
    <h3>KERATIN</h3><p>Nemo enim ipsam voluptatem quia volup-<br>tas sit aspernatur aut odit aut</p><div class="btn">Read More ▸</div>
  </div>
  <div class="abs card" style="left:846px;top:147px">
    <div class="photo" role="img" aria-label="Makeup artist applying eye makeup" style="background:linear-gradient(120deg,#7a5040,#d0a088 50%,#8a6a60)"></div>
    <h3>MAKEUP</h3><p>Nemo enim ipsam voluptatem quia volup-<br>tas sit aspernatur aut odit aut</p><div class="btn">Read More ▸</div>
  </div>
</section>

<h2 class="abs section-title gallery-title">←&nbsp;&nbsp; OUR GALLERY &nbsp;&nbsp;→</h2>
<div class="abs shot" style="left:132px;background:linear-gradient(120deg,#9a9a9a,#8a4a30 50%,#5e2d1c)" role="img" aria-label="Woman with long auburn curls"></div>
<div class="abs shot" style="left:451px;background:linear-gradient(120deg,#d8d8d8,#6a4030 50%,#c49a84)" role="img" aria-label="Woman with windswept brown hair"></div>
<div class="abs shot" style="left:769px;background:linear-gradient(120deg,#e4e1c8,#8a4630 50%,#d6b3a0)" role="img" aria-label="Woman with curls and manicured nails"></div>

<footer class="abs footer">
  <div class="abs brand" style="left:131px;top:58px">Quill Petal Loft</div>
  <p class="abs blurb">We all know how glamorous Englewood is, but we needed a place for a quick fix where women could take their bed head from flat to fab in less than an hour</p>
  <h4 class="abs">CONTACT US</h4>
  <div class="abs loc" style="left:453px;top:80px"><svg class="icon" viewBox="0 0 10 10" style="margin-top:4px;flex:none"><path d="M5 0a3.5 3.5 0 0 1 3.5 3.5C8.5 6 5 10 5 10S1.5 6 1.5 3.5A3.5 3.5 0 0 1 5 0z"/></svg><span>14 Linden Row, Englewood,<br>NJ</span></div>
  <div class="abs loc" style="left:672px;top:80px"><svg class="icon" viewBox="0 0 10 10" style="margin-top:4px;flex:none"><path d="M5 0a3.5 3.5 0 0 1 3.5 3.5C8.5 6 5 10 5 10S1.5 6 1.5 3.5A3.5 3.5 0 0 1 5 0z"/></svg><span>280 Grand Avenue, Engle-<br>wood, NJ</span></div>
  <div class="abs loc" style="left:855px;top:80px"><svg class="icon" viewBox="0 0 10 10" style="margin-top:4px;flex:none"><path d="M5 0a3.5 3.5 0 0 1 3.5 3.5C8.5 6 5 10 5 10S1.5 6 1.5 3.5A3.5 3.5 0 0 1 5 0z"/></svg><span>77 Palisade Ave, Engle-<br>wood, NJ</span></div>
  <div class="abs loc" style="left:453px;top:134px"><svg class="icon" viewBox="0 0 10 10" style="margin-top:4px;flex:none"><path d="M2 0l2 2-1 1.5c.8 1.5 2 2.7 3.5 3.5L8 6l2 2-1.5 2C4 9.5.5 6 0 1.5z"/></svg><span>201.555.0182</span></div>
  <div class="abs loc" style="left:672px;top:134px"><svg class="icon" viewBox="0 0 10 10" style="margin-top:4px;flex:none"><path d="M2 0l2 2-1 1.5c.8 1.5 2 2.7 3.5 3.5L8 6l2 2-1.5 2C4 9.5.5 6 0 1.5z"/></svg><span>201.555.0140</span></div>
  <div class="abs loc" style="left:855px;top:134px"><svg class="icon" viewBox="0 0 10 10" style="margin-top:4px;flex:none"><path d="M2 0l2 2-1 1.5c.8 1.5 2 2.7 3.5 3.5L8 6l2 2-1.5 2C4 9.5.5 6 0 1.5z"/></svg><span>201.555.0167</span></div>
  <div class="abs rule"></div>
  <div class="abs copy">© 2016 quillpetalloft.com. All rights reserved.</div>
  <div class="abs social" style="left:972px;top:269px"><span></span><span></span><span></span><span></span></div>
</footer>

</body>
</html>
```